Business Card for beauty technology startup

Design Glimora Business Card for a Beauty, based on the website identity and colors (https://www.glimora-example.com).
Glimora is a beauty tech startup that gathers helpful product info for beauty lovers and consumers (such as availability on stores, price range and product reviews) for makeup products. The card design must be young, colorful but clean, and very modern.

Target Market(s)

woman, 15-35

Industry/Entity Type

Cosmetics

Contact Information for Business Card

Full Name, address, phone

Font styles to use
Other font styles liked:
• Advent Pro

Colors
e34297
86cfc6
ffffff
5c5c5c
e8e8e8
e667a6
b2b2b2

Requirements
Must have
• One full colored side with a creative design and another with card info
• Use Color palette: #95C5C5 and/or #D38AA5
• Use fonts: Advent Pro
• Use website identity: https://www.glimora-example.com
Nice to have
• If needed extra font: Roboto

```html
<!DOCTYPE html>
<html lang="en">
<head>
<meta charset="utf-8">
<title>Glimora Business Card</title>
<link rel="stylesheet" href="https://fonts.googleapis.com/css2?family=Advent+Pro:wght@200;300;500&family=Roboto:wght@400;500&family=Roboto+Condensed:wght@500&display=swap">
<style>
  :root {
    --backdrop: #e8e8e8;
    --card-white: #ffffff;
    --teal: #86cfc6;
    --teal-soft: #95c5c5;
    --pink: #e34297;
    --pink-mid: #e667a6;
    --pink-soft: #d38aa5;
    --ink: #5c5c5c;
    --light-grey: #b2b2b2;
    --white: #ffffff;
  }
  * { box-sizing: border-box; margin: 0; padding: 0; }
  html, body { width: 1200px; height: 960px; overflow: hidden; background: var(--backdrop); }
  .stage { position: relative; width: 1200px; height: 960px; }

  .card { position: absolute; width: 600px; height: 342px; border-radius: 16px; overflow: hidden; box-shadow: 0 4px 10px rgba(0,0,0,.16); }
  .card-front { left: 315px; top: 113px; background: var(--card-white); }
  .card-back { left: 311px; top: 472px; height: 340px; background: linear-gradient(135deg, var(--pink-soft) 0%, var(--pink-mid) 55%, var(--pink) 100%); }

  .card-shapes { position: absolute; inset: 0; width: 100%; height: 100%; }

  .holder { position: absolute; right: 33px; top: 24px; text-align: right; color: var(--white); font-family: "Roboto Condensed", sans-serif; font-weight: 500; }
  .holder-name { font-size: 20px; letter-spacing: .3px; }
  .holder-title { font-size: 14.5px; margin-top: 4px; letter-spacing: .3px; }

  .brand { position: absolute; left: 46px; top: 112px; display: flex; align-items: center; gap: 14px; }
  .brand-dot { width: 44px; height: 44px; border-radius: 50%; background: var(--teal); }
  .brand-name { font-family: "Advent Pro", sans-serif; font-weight: 300; font-size: 44px; letter-spacing: 4px; color: var(--pink); }

  .contacts { position: absolute; left: 134px; top: 208px; list-style: none; font-family: "Roboto", sans-serif; font-size: 14px; color: var(--ink); }
  .contacts li { display: flex; align-items: center; height: 19px; }
  .contacts svg { width: 12px; height: 12px; margin-right: 9px; fill: var(--pink); }

  .address { position: absolute; right: 34px; top: 266px; text-align: right; font-family: "Roboto", sans-serif; font-size: 14px; line-height: 19px; color: var(--ink); font-style: normal; }

  .back-brand { position: absolute; right: 33px; top: 240px; text-align: right; }
  .back-brand-name { font-family: "Advent Pro", sans-serif; font-weight: 300; font-size: 54px; letter-spacing: 5px; color: var(--white); line-height: 1; }
  .back-brand-url { font-family: "Roboto", sans-serif; font-size: 12px; letter-spacing: 3px; color: var(--white); margin-top: 6px; }
</style>
</head>
<body>
<main class="stage">

  <section class="card card-front" aria-label="Card front">
    <svg class="card-shapes" viewBox="0 0 600 342" aria-hidden="true">
      <rect width="600" height="180" fill="var(--teal)"/>
      <path d="M88 52 C250 8 450 0 600 0 L600 170 C480 62 300 30 88 52 Z" fill="var(--pink-mid)"/>
      <path d="M88 52 C250 8 450 0 600 0" fill="none" stroke="var(--white)" stroke-width="3"/>
      <path d="M0 118 C110 48 300 20 430 52 C510 72 565 120 600 170 L600 342 L0 342 Z" fill="var(--card-white)"/>
      <rect y="334" width="600" height="8" fill="var(--teal-soft)"/>
    </svg>

    <div class="holder">
      <div class="holder-name">MAYA LINWOOD</div>
      <div class="holder-title">CEO/FOUNDER</div>
    </div>

    <div class="brand">
      <span class="brand-dot" aria-hidden="true"></span>
      <span class="brand-name">GLIMORA</span>
    </div>

    <ul class="contacts">
      <li><svg viewBox="0 0 12 12"><path d="M2.5 0.5 L4.5 0.5 L5 3.5 L3.7 4.5 C4.4 6 5.8 7.4 7.5 8.3 L8.5 7 L11.5 7.5 L11.5 9.5 C11.5 10.8 10.5 11.5 9 11.3 C4.5 10.5 1.3 7.3 0.6 3 C0.4 1.5 1.2 0.5 2.5 0.5 Z"/></svg>555 210 4836</li>
      <li><svg viewBox="0 0 12 12"><path d="M3 0 H9 A1 1 0 0 1 10 1 V11 A1 1 0 0 1 9 12 H3 A1 1 0 0 1 2 11 V1 A1 1 0 0 1 3 0 Z M3.2 1.5 V9.5 H8.8 V1.5 Z"/></svg>555 318 7204</li>
      <li><svg viewBox="0 0 12 12"><path d="M3 0 H9 V3 H3 Z M0.5 4 H11.5 V9 H9.5 V7 H2.5 V9 H0.5 Z M3 8 H9 V12 H3 Z"/></svg>555 462 9015</li>
      <li><svg viewBox="0 0 12 12"><path d="M0 2 H12 V10 H0 Z M0.8 2.6 L6 6.5 L11.2 2.6" stroke="var(--card-white)" stroke-width=".9"/></svg>info@glimora-example.com</li>
      <li><svg viewBox="0 0 12 12"><circle cx="6" cy="6" r="5.5"/><path d="M6 0.5 V11.5 M0.5 6 H11.5" stroke="var(--card-white)" stroke-width=".9"/></svg>www.glimora-example.com</li>
    </ul>

    <address class="address">
      2146 Willowbend Court<br>
      Fairview, Oregon 97024
    </address>
  </section>

  <section class="card card-back" aria-label="Card back">
    <svg class="card-shapes" viewBox="0 0 600 340" aria-hidden="true">
      <path d="M0 0 H260 C200 90 150 200 0 260 Z" fill="var(--teal)"/>
      <path d="M0 0 H170 C130 70 90 140 0 180 Z" fill="var(--teal-soft)" opacity=".8"/>
      <path d="M0 272 C170 210 230 90 285 0" fill="none" stroke="var(--white)" stroke-width="3"/>
      <circle cx="470" cy="70" r="120" fill="var(--white)" opacity=".08"/>
      <circle cx="540" cy="20" r="60" fill="var(--white)" opacity=".1"/>
    </svg>
    <div class="back-brand">
      <div class="back-brand-name">GLIMORA</div>
      <div class="back-brand-url">www.glimora-example.com</div>
    </div>
  </section>

</main>
</body>
</html>
```